New Business Card Design Project LORVANTI-Italy

we are LORVANTI-Italy
our company in the market for 3 years we are luxury cosmetic company and its about time for a facelift :)
i will like to have elegant luxurious and unique business card
that will give the person that get it a unique, luxurious and elegant impression
I'm VERY OPEN FOR NEW IDEAS , even duo i add a few files of things that i see on line and i like them

i add my logo as well
my website is LORVANTI.COM
(if you would like to see the main style that we have)

Target Market(s)

adult that have money :)

Industry/Entity Type

Business

Contact Information for Business Card

Name - Dario Lorvanti
Position - CEO and CO Founder
address - 4817 E Halvern
telephone - 555-384-1926
email - dario@lorvanti.com
fax - 555-384-1926
website - LORVANTI.COM

Colors
000000
959595
fbee3e
ffffff

Requirements
Must have
• big logo in GOLD color
• elegant look
• impressive
Nice to have
• not must but maybe classy pattern background
• not must but maybe emblem
• maybe clear plastic business card
Should not have
• colors
• images

```html
<!DOCTYPE html>
<html lang="en">
<head>
<meta charset="utf-8">
<title>LORVANTI-Italy Business Card</title>
<link href="https://fonts.googleapis.com/css2?family=Roboto:wght@400;500&family=Roboto+Condensed:wght@700&display=swap" rel="stylesheet">
<style>
  :root {
    --backdrop: #2b2b2b;
    --card: #1c1c1c;
    --gold: #d8b443;
    --gold-light: #f1d66a;
    --white: #ffffff;
    --grey: #959595;
  }
  * { margin: 0; padding: 0; box-sizing: border-box; }
  html, body { width: 1200px; height: 900px; overflow: hidden; }
  body {
    background: var(--backdrop);
    font-family: "Roboto", Arial, sans-serif;
    display: flex;
    flex-direction: column;
    align-items: center;
    justify-content: center;
    gap: 50px;
  }
  .card {
    width: 640px;
    height: 366px;
    background: var(--card);
    position: relative;
    box-shadow: 0 8px 24px rgba(0,0,0,0.45);
  }
  /* Front */
  .card-front {
    display: flex;
    flex-direction: column;
    align-items: center;
    justify-content: center;
  }
  .brand-mark {
    width: 86px;
    height: 86px;
    border: 3px solid var(--gold);
    border-radius: 50%;
    margin-bottom: 26px;
  }
  .brand-name {
    color: var(--gold);
    font-weight: 500;
    font-size: 40px;
    letter-spacing: 3px;
  }
  .website {
    margin-top: 26px;
    color: var(--white);
    font-size: 15px;
    letter-spacing: 6px;
  }
  /* Back */
  .card-back { padding: 0; }
  .identity {
    position: absolute;
    right: 346px;
    top: 108px;
    text-align: right;
  }
  .person-name {
    font-family: "Roboto Condensed", "Arial Narrow", sans-serif;
    font-weight: 700;
    font-size: 38px;
    color: var(--gold);
    line-height: 1.1;
  }
  .person-title {
    color: var(--white);
    font-size: 17px;
    margin-top: 6px;
  }
  .divider {
    position: absolute;
    left: 310px;
    top: 92px;
    width: 2px;
    height: 118px;
    background: linear-gradient(to bottom, transparent, var(--grey) 30%, var(--grey) 70%, transparent);
  }
  .contact-list {
    position: absolute;
    left: 332px;
    top: 96px;
    list-style: none;
  }
  .contact-list li {
    display: flex;
    align-items: center;
    gap: 10px;
    color: var(--white);
    font-size: 17px;
    height: 27px;
  }
  .icon { width: 17px; height: 17px; fill: var(--gold); flex: none; }
  .address {
    position: absolute;
    left: 0; right: 0;
    bottom: 70px;
    display: flex;
    justify-content: center;
    align-items: center;
    gap: 10px;
    color: var(--white);
    font-size: 17px;
  }
  .address .icon { width: 18px; height: 24px; }
</style>
</head>
<body>
  <section class="card card-front">
    <div class="brand-mark"></div>
    <div class="brand-name">LORVANTI-Italy</div>
    <div class="website">www.lorvanti.com</div>
  </section>

  <section class="card card-back">
    <div class="identity">
      <div class="person-name">Dario Lorvanti</div>
      <div class="person-title">CEO &amp; CO Founder</div>
    </div>
    <div class="divider"></div>
    <ul class="contact-list">
      <li>
        <svg class="icon" viewBox="0 0 24 24" aria-hidden="true"><path d="M6.6 10.8a15.1 15.1 0 0 0 6.6 6.6l2.2-2.2c.3-.3.7-.4 1-.2 1.1.4 2.3.6 3.6.6.6 0 1 .4 1 1V20c0 .6-.4 1-1 1C10.6 21 3 13.4 3 4c0-.6.4-1 1-1h3.5c.6 0 1 .4 1 1 0 1.3.2 2.5.6 3.6.1.3 0 .7-.2 1z"/></svg>
        555-384-1926
      </li>
      <li>
        <svg class="icon" viewBox="0 0 24 24" aria-hidden="true"><path d="M6 2h10l2 2v5H6z M3 10h18v9H3z M6 15h12v7H6z"/></svg>
        555-384-1926
      </li>
      <li>
        <svg class="icon" viewBox="0 0 24 24" aria-hidden="true"><path d="M2 5h20v14H2z M3 6l9 7 9-7" stroke="#1c1c1c" stroke-width="1.5"/></svg>
        dario@lorvanti.com
      </li>
      <li>
        <svg class="icon" viewBox="0 0 24 24" aria-hidden="true"><circle cx="12" cy="12" r="10"/><path d="M2 12h20 M12 2c3 3 3 17 0 20 M12 2c-3 3-3 17 0 20" stroke="#1c1c1c" stroke-width="1.4" fill="none"/></svg>
        LORVANTI.COM
      </li>
    </ul>
    <div class="address">
      <svg class="icon" viewBox="0 0 18 24" aria-hidden="true"><path d="M9 0a9 9 0 0 0-9 9c0 6.5 9 15 9 15s9-8.5 9-15a9 9 0 0 0-9-9zm0 12.5A3.5 3.5 0 1 1 9 5.5a3.5 3.5 0 0 1 0 7z"/></svg>
      4817 E Halvern
    </div>
  </section>
</body>
</html>
```